CBD/HEMP website for e-commerce store

I need a CBD website for my shopify store. I am looking for a layout similar to these site ( https://quietmeadowcbd.com/ ) (https://elmridgecbd.com/) but with my logo and products. I am attaching what my logo looks like so that it helps with the design.

Target Market(s)

CBD HEMP CANNABIS

Industry/Entity Type

Cannabis

Coding

Coded - Design and coding required

Number of Pages Required

5+ page

Requirements
Nice to have
• I would like for it to have a trendy/galaxy feel

```html
<!DOCTYPE html>
<html lang="en">
<head>
<meta charset="utf-8">
<title>Orbit Leaf CBD Store – Home Concepts</title>
<link href="https://fonts.googleapis.com/css2?family=Poppins:wght@300;400;500;600&display=swap" rel="stylesheet">
<style>
:root{
  --purple:#9b1fa8;
  --purple-deep:#5a1670;
  --pink:#e0156b;
  --black:#050507;
  --green:#3fbf2a;
  --ink:#111;
  --muted:#666;
  --white:#fff;
  --galaxy:radial-gradient(ellipse at 70% 30%,#c2368e 0%,rgba(194,54,142,0) 35%),radial-gradient(ellipse at 20% 60%,#2f5fb8 0%,rgba(47,95,184,0) 40%),radial-gradient(ellipse at 50% 90%,#6a2aa8 0%,rgba(106,42,168,0) 45%),linear-gradient(160deg,#0b0d2a,#1a1044 50%,#0a0820);
  --card-galaxy:radial-gradient(circle at 40% 40%,#6b48c4,#2b1a6a 60%,#160d3a);
}
*{box-sizing:border-box;margin:0;padding:0}
html,body{width:1033px;height:1200px;overflow:hidden;background:#fff}
body{position:relative;font-family:"Poppins",sans-serif}
.page{position:absolute;top:30px;width:517px;height:1968px;transform:scale(.58);transform-origin:0 0;overflow:hidden;box-shadow:1px 1px 3px rgba(0,0,0,.25)}
.p1{left:43px}.p2{left:367px}.p3{left:691px}
.a{position:absolute}
.light{background:var(--white);color:var(--ink)}
.galaxy{background:var(--galaxy);color:var(--white)}

.topbar{top:0;left:0;width:517px;height:16px;background:var(--purple);color:#fff;font-size:6px;display:flex;align-items:center;padding:0 38px}
.topbar .promo{margin-left:auto;margin-right:46px}
.topbar .tools{display:flex;gap:13px}
.nav{top:16px;left:0;width:517px;height:53px;background:var(--black);color:#fff;font-size:6px}
.nav .links{position:absolute;top:23px;display:flex;gap:17px}
.brand{position:absolute;left:209px;top:18px;width:100px;display:flex;align-items:center;gap:4px;font-size:10px;font-weight:500;color:#c83fd0}
.brand i{display:block;width:9px;height:9px;border-radius:50%;background:#c83fd0}

.hero{top:69px;left:0;width:517px;height:340px;background:var(--galaxy)}
.hero h1{position:absolute;left:38px;top:128px;font-size:20px;font-weight:500;line-height:25px;color:#fff;letter-spacing:.3px}
.btn{background:var(--pink);color:#fff;font-size:5px;display:flex;align-items:center;justify-content:center;text-transform:uppercase}
.hero .btn{position:absolute;left:38px;top:190px;width:72px;height:17px}
.bottles{position:absolute;left:340px;top:41px;width:135px;height:255px;border-radius:30px 30px 8px 8px;background:linear-gradient(180deg,#2a2a2a 0 22%,#b8a535 22%,#d9cc55 60%,#8a6a2a)}

.cat{width:143px;height:97px;top:450px}
.cat-label{top:550px;width:143px;text-align:center;font-size:8.5px;letter-spacing:.4px}
.flowers{background:linear-gradient(135deg,#1d6fb0,#7fb1c7 40%,#6c6a3a 70%,#2a3a22)}
.vapes{background:linear-gradient(135deg,#f2f2f2,#9aa 45%,#d4471b 70%,#222)}
.oils{background:linear-gradient(135deg,#9fcf5a,#3e7a25 55%,#5a2d12)}

.sect-icon{left:251px;width:15px;height:15px;border-radius:50%;background:var(--green);box-shadow:0 0 6px #6f6}
.sect-title{left:0;width:517px;text-align:center;font-size:14px;font-weight:500;letter-spacing:.6px}

.prod{top:630px;width:106px;height:133px;display:flex;align-items:center;justify-content:center}
.light .prod,.light .deal{background:var(--card-galaxy)}
.galaxy .prod,.galaxy .deal{background:#fff}
.obj{width:40px;height:90px;border-radius:14px 14px 6px 6px;background:linear-gradient(180deg,#222 0 25%,#c9a33a 25%,#6b3d10)}
.obj.bud{width:62px;height:40px;border-radius:50%;background:radial-gradient(circle,#9aa04a,#5c6a22)}
.obj.nug{width:44px;height:60px;border-radius:45%;background:radial-gradient(circle,#b99b55,#6b5a2a)}
.pname{font-size:6px}
.price{font-size:5.5px;color:#c13ab8}

.band{top:841px;left:0;width:517px;height:178px;background:radial-gradient(ellipse at 50% 50%,#111 0 25%,rgba(0,0,0,0) 55%),linear-gradient(135deg,#2f5e22,#0d1a0a 35%,#3e7a2a 60%,#0c1408)}
.band h2{position:absolute;top:62px;width:517px;text-align:center;color:#fff;font-size:15px;font-weight:400;letter-spacing:.5px}
.band .btn{position:absolute;left:222px;top:93px;width:72px;height:17px}

.feat-img{left:38px;top:1114px;width:220px;height:198px;background:radial-gradient(circle at 45% 55%,#d8e04a,#8a9a1a 35%,#2e3a12 60%,#0e120a)}
.feat{left:278px;top:1112px;width:200px}
.feat h3{font-size:11px;font-weight:400}
.feat .cost{font-size:7px;margin-top:4px}
.feat .qty{font-size:6px;margin-top:8px}
.select{height:15px;background:#e3e3e3;margin-top:6px;position:relative}
.select:after{content:"⌄";position:absolute;right:5px;top:0;font-size:7px;color:#333}
.feat .btn{height:16px;margin-top:6px}
.feat .btn.alt{background:var(--purple)}
.feat p{font-size:5.3px;line-height:9.2px;margin-top:11px;text-align:justify;color:var(--muted)}
.galaxy .feat p{color:#e6e0ef}

.deal{top:1399px;width:143px;height:184px;display:flex;align-items:center;justify-content:center;position:absolute}
.deal .obj{height:120px;width:50px}
.deal .mod{background:linear-gradient(90deg,#999,#f4f4f4 40%,#aaa)}
.deal .dropper{background:linear-gradient(180deg,#2a7a3a 0 15%,#eee 15% 30%,#e07020 30%,#8a3010)}
.deal-name{position:absolute;width:143px;text-align:center;font-size:7px}
.light .deal-name{top:88px;color:#fff}
.galaxy .deal-name{top:168px;color:#222}

.news{top:1624px;left:0;width:517px;height:189px;background:radial-gradient(ellipse at 30% 40%,#b13ac0,rgba(177,58,192,0) 55%),linear-gradient(120deg,#7a1a8e,#4c1468 60%,#8e2aa0);color:#fff}
.news .t{position:absolute;top:70px;width:517px;text-align:center;font-size:14px;font-weight:500;letter-spacing:.6px}
.news p{position:absolute;top:91px;left:115px;width:287px;text-align:center;font-size:6.5px;line-height:9.5px}
.news .field{position:absolute;left:102px;top:121px;width:242px;height:19px;background:#fff;color:#888;font-size:5px;padding:7px 6px}
.news .btn{position:absolute;left:344px;top:121px;width:70px;height:19px}

.foot{top:1813px;left:0;width:517px;height:155px}
.light .foot{background:#fff;color:#222}
.galaxy .foot{background:linear-gradient(180deg,#0a0a14,#050507);color:#fff}
.foot h4{position:absolute;top:35px;font-size:6px;font-weight:600;letter-spacing:.4px}
.foot ul{position:absolute;top:56px;list-style:none;font-size:5.5px;line-height:9.4px}
.foot .about{position:absolute;left:38px;top:56px;width:120px;font-size:5.5px;line-height:9.4px}
.dot{display:inline-block;width:4px;height:4px;border-radius:50%;background:currentColor;margin-right:5px;vertical-align:middle}
.pay{position:absolute;top:127px;left:215px;display:flex;gap:4px}
.pay span{width:10px;height:6px;border-radius:1px;background:#777}
.galaxy .pay span{background:#ddd}
.copy{position:absolute;top:139px;width:517px;text-align:center;font-size:5.3px}

.overlay{top:0;left:0;width:517px;height:1968px;background:rgba(0,0,0,.72)}
.modal{left:149px;top:84px;width:247px;height:158px;background:var(--pink);color:#fff}
.modal .close{position:absolute;right:6px;top:2px;font-size:6px}
.modal h2{position:absolute;top:56px;width:247px;text-align:center;font-size:13px;font-weight:600;letter-spacing:.5px}
.modal .yes,.modal .no{position:absolute;top:83px;height:15px;font-size:6px;display:flex;align-items:center;justify-content:center}
.modal .yes{left:65px;width:49px;background:#fff;color:var(--pink)}
.modal .no{left:119px;width:35px;border:1px solid #fff}
</style>
</head>
<body>

<!-- Concept 1: light -->
<section class="page p1 light">
  <div class="a topbar"><span>⌕ Search</span><span class="promo">Free delivery on all orders over $60</span><span class="tools"><span>Login</span><span>$ USD ⌄</span><span>Cart (0)</span></span></div>
  <nav class="a nav"><div class="links" style="left:38px"><span>Home</span><span>Shop</span><span>Blog</span></div><div class="brand"><i></i>Orbit Leaf</div><div class="links" style="left:389px"><span>Categories</span><span>Contact Us</span></div></nav>
  <div class="a hero" role="img" aria-label="Galaxy background with CBD oil bottles"><h1>Shop The<br>Orbit Leaf CBD/Hemp</h1><div class="btn">Shop Now</div><div class="bottles"></div></div>
  <div class="a cat flowers" style="left:38px" role="img" aria-label="CBD flower buds"></div>
  <div class="a cat vapes" style="left:187px" role="img" aria-label="CBD vape pens and bottles"></div>
  <div class="a cat oils" style="left:335px" role="img" aria-label="Hemp oil with dropper"></div>
  <div class="a cat-label" style="left:38px">CBD Flowers</div><div class="a cat-label" style="left:187px">CBD Vapes</div><div class="a cat-label" style="left:335px">HEMP Oils</div>
  <div class="a sect-icon" style="top:602px"></div><div class="a sect-title" style="top:620px">OUR PRODUCTS</div>
  <div class="a prod" style="left:38px;top:648px"><div class="obj" role="img" aria-label="Hemp oil bottle"></div></div>
  <div class="a prod" style="left:149px;top:648px"><div class="obj bud" role="img" aria-label="CBD bud"></div></div>
  <div class="a prod" style="left:260px;top:648px"><div class="obj" role="img" aria-label="Hemp oil bottle"></div></div>
  <div class="a prod" style="left:371px;top:648px"><div class="obj nug" role="img" aria-label="CBD flower"></div></div>
  <div class="a pname" style="left:38px;top:785px">Product Name<div class="price">$21.00</div></div>
  <div class="a pname" style="left:149px;top:785px">Product Name<div class="price">$21.00</div></div>
  <div class="a pname" style="left:260px;top:785px">Product Name<div class="price">$21.00</div></div>
  <div class="a pname" style="left:371px;top:785px">Product Name<div class="price">$21.00</div></div>
  <div class="a band" role="img" aria-label="Cannabis leaves"><h2>BEYOND THE HIGH</h2><div class="btn">Shop Now</div></div>
  <div class="a sect-icon" style="top:1062px"></div><div class="a sect-title" style="top:1080px">FEATURED PRODUCTS</div>
  <div class="a feat-img" role="img" aria-label="Jar of CBD oil with hemp leaf"></div>
  <div class="a feat"><h3>Lorem ipsum dolor</h3><div class="cost">$5.00</div><div class="qty">Quantity</div><div class="select"></div><div class="btn">Buy Now</div><div class="btn alt">Add To Cart</div><p>Lorem ipsum dolor sit amet, consectetur adipiscing elit, sed do eiusmod tempor incididunt ut labore et dolore magna aliqua. Ut enim ad minim veniam, quis nostrud exercitation ullamco laboris nisi ut aliquip ex ea commodo consequat. Duis aute irure dolor in reprehenderit in voluptate velit esse cillum dolore eu fugiat nulla pariatur. Excepteur sint occaecat cupidatat non proident, sunt in culpa qui officia deserunt mollit anim id est laborum</p></div>
  <div class="a sect-icon" style="top:1355px"></div><div class="a sect-title" style="top:1373px">BEST DEAL</div>
  <div class="deal" style="left:38px"><div class="obj mod" role="img" aria-label="Vape mod"></div><div class="deal-name">Product Name</div></div>
  <div class="deal" style="left:187px"><div class="obj dropper" role="img" aria-label="CBD oil with bud"></div><div class="deal-name">Product Name</div></div>
  <div class="deal" style="left:335px"><div class="obj" role="img" aria-label="Hemp oil bottle"></div><div class="deal-name">Product Name</div></div>
  <div class="a news"><div class="a sect-icon" style="top:50px"></div><div class="t">SUBSCRIBE OUR NEWSLETTER</div><p>Lorem ipsum dolor sit amet, consectetur adipiscing elit, sed do eiusmod tempor incididunt ut labore et dolore magna aliqua.</p><div class="field">Enter Your Email Address</div><div class="btn">Join</div></div>
  <footer class="a foot"><h4 style="left:38px">ABOUT US</h4><div class="about">Lorem ipsum dolor sit amet, consectetur adipiscing elit, sed do eiusmod tempor incididunt ut labore et dolore magna aliqua.</div><h4 style="left:213px">PRODUCTS</h4><ul style="left:213px"><li>CBD Flowers</li><li>CBD Vapes</li><li>HEMP Oils</li></ul><h4 style="left:327px">EXPLORE</h4><ul style="left:327px"><li>Home</li><li>About Us</li><li>Shop</li><li>Categories</li><li>Contact Us</li></ul><h4 style="left:436px">FOLLOW US</h4><ul style="left:436px"><li><span class="dot"></span>Pixelpost</li><li><span class="dot"></span>Chatterbox</li><li><span class="dot"></span>Snapgrid</li><li><span class="dot"></span>Worklink</li></ul><div class="pay"><span></span><span></span><span></span><span></span><span></span><span></span></div><div class="copy">© Copyrights 2021 The Company Name All Rights Reserved</div></footer>
</section>

<!-- Concept 2: age gate over galaxy theme -->
<section class="page p2 galaxy">
  <div class="a topbar"><span>⌕ Search</span><span class="promo">Free delivery on all orders over $60</span><span class="tools"><span>Login</span><span>$ USD ⌄</span><span>Cart (0)</span></span></div>
  <nav class="a nav"><div class="links" style="left:38px"><span>Home</span><span>Shop</span><span>Blog</span></div><div class="brand"><i></i>Orbit Leaf</div><div class="links" style="left:389px"><span>Categories</span><span>Contact Us</span></div></nav>
  <div class="a hero" role="img" aria-label="Galaxy background with CBD oil bottles"><h1>Shop The<br>Orbit Leaf CBD/Hemp</h1><div class="btn">Shop Now</div><div class="bottles"></div></div>
  <div class="a cat flowers" style="left:38px" role="img" aria-label="CBD flower buds"></div>
  <div class="a cat vapes" style="left:187px" role="img" aria-label="CBD vape pens and bottles"></div>
  <div class="a cat oils" style="left:335px" role="img" aria-label="Hemp oil with dropper"></div>
  <div class="a cat-label" style="left:38px">CBD Flowers</div><div class="a cat-label" style="left:187px">CBD Vapes</div><div class="a cat-label" style="left:335px">HEMP Oils</div>
  <div class="a sect-icon" style="top:602px"></div><div class="a sect-title" style="top:620px">OUR PRODUCTS</div>
  <div class="a prod" style="left:38px;top:648px"><div class="obj" role="img" aria-label="Hemp oil bottle"></div></div>
  <div class="a prod" style="left:149px;top:648px"><div class="obj bud" role="img" aria-label="CBD bud"></div></div>
  <div class="a prod" style="left:260px;top:648px"><div class="obj" role="img" aria-label="Hemp oil bottle"></div></div>
  <div class="a prod" style="left:371px;top:648px"><div class="obj nug" role="img" aria-label="CBD flower"></div></div>
  <div class="a pname" style="left:38px;top:785px">Product Name<div class="price">$21.00</div></div>
  <div class="a pname" style="left:149px;top:785px">Product Name<div class="price">$21.00</div></div>
  <div class="a pname" style="left:260px;top:785px">Product Name<div class="price">$21.00</div></div>
  <div class="a pname" style="left:371px;top:785px">Product Name<div class="price">$21.00</div></div>
  <div class="a band" role="img" aria-label="Cannabis leaves"><h2>BEYOND THE HIGH</h2><div class="btn">Shop Now</div></div>
  <div class="a sect-icon" style="top:1062px"></div><div class="a sect-title" style="top:1080px">FEATURED PRODUCTS</div>
  <div class="a feat-img" role="img" aria-label="Jar of CBD oil with hemp leaf"></div>
  <div class="a feat"><h3>Lorem ipsum dolor</h3><div class="cost">$5.00</div><div class="qty">Quantity</div><div class="select"></div><div class="btn">Buy Now</div><div class="btn alt">Add To Cart</div><p>Lorem ipsum dolor sit amet, consectetur adipiscing elit, sed do eiusmod tempor incididunt ut labore et dolore magna aliqua. Ut enim ad minim veniam, quis nostrud exercitation ullamco laboris nisi ut aliquip ex ea commodo consequat. Duis aute irure dolor in reprehenderit in voluptate velit esse cillum dolore eu fugiat nulla pariatur. Excepteur sint occaecat cupidatat non proident, sunt in culpa qui officia deserunt mollit anim id est laborum</p></div>
  <div class="a sect-icon" style="top:1355px"></div><div class="a sect-title" style="top:1373px">BEST DEAL</div>
  <div class="deal" style="left:38px"><div class="obj mod" role="img" aria-label="Vape mod"></div><div class="deal-name">Product Name</div></div>
  <div class="deal" style="left:187px"><div class="obj dropper" role="img" aria-label="CBD oil with bud"></div><div class="deal-name">Product Name</div></div>
  <div class="deal" style="left:335px"><div class="obj" role="img" aria-label="Hemp oil bottle"></div><div class="deal-name">Product Name</div></div>
  <div class="a news"><div class="a sect-icon" style="top:50px"></div><div class="t">SUBSCRIBE OUR NEWSLETTER</div><p>Lorem ipsum dolor sit amet, consectetur adipiscing elit, sed do eiusmod tempor incididunt ut labore et dolore magna aliqua.</p><div class="field">Enter Your Email Address</div><div class="btn">Join</div></div>
  <footer class="a foot"><h4 style="left:38px">ABOUT US</h4><div class="about">Lorem ipsum dolor sit amet, consectetur adipiscing elit, sed do eiusmod tempor incididunt ut labore et dolore magna aliqua.</div><h4 style="left:213px">PRODUCTS</h4><ul style="left:213px"><li>CBD Flowers</li><li>CBD Vapes</li><li>HEMP Oils</li></ul><h4 style="left:327px">EXPLORE</h4><ul style="left:327px"><li>Home</li><li>About Us</li><li>Shop</li><li>Categories</li><li>Contact Us</li></ul><h4 style="left:436px">FOLLOW US</h4><ul style="left:436px"><li><span class="dot"></span>Pixelpost</li><li><span class="dot"></span>Chatterbox</li><li><span class="dot"></span>Snapgrid</li><li><span class="dot"></span>Worklink</li></ul><div class="pay"><span></span><span></span><span></span><span></span><span></span><span></span></div><div class="copy">© Copyrights 2021 The Company Name All Rights Reserved</div></footer>
  <div class="a overlay"></div>
  <div class="a modal" role="dialog" aria-label="Age check"><span class="close">x</span><h2>ARE YOU 18+ &amp; ABOVE</h2><div class="yes">YES</div><div class="no">NO</div></div>
</section>

<!-- Concept 3: galaxy -->
<section class="page p3 galaxy">
  <div class="a topbar"><span>⌕ Search</span><span class="promo">Free delivery on all orders over $60</span><span class="tools"><span>Login</span><span>$ USD ⌄</span><span>Cart (0)</span></span></div>
  <nav class="a nav"><div class="links" style="left:38px"><span>Home</span><span>Shop</span><span>Blog</span></div><div class="brand"><i></i>Orbit Leaf</div><div class="links" style="left:389px"><span>Categories</span><span>Contact Us</span></div></nav>
  <div class="a hero" role="img" aria-label="Galaxy background with CBD oil bottles"><h1>Shop The<br>Orbit Leaf CBD/Hemp</h1><div class="btn">Shop Now</div><div class="bottles"></div></div>
  <div class="a cat flowers" style="left:38px" role="img" aria-label="CBD flower buds"></div>
  <div class="a cat vapes" style="left:187px" role="img" aria-label="CBD vape pens and bottles"></div>
  <div class="a cat oils" style="left:335px" role="img" aria-label="Hemp oil with dropper"></div>
  <div class="a cat-label" style="left:38px">CBD Flowers</div><div class="a cat-label" style="left:187px">CBD Vapes</div><div class="a cat-label" style="left:335px">HEMP Oils</div>
  <div class="a sect-icon" style="top:602px"></div><div class="a sect-title" style="top:620px">OUR PRODUCTS</div>
  <div class="a prod" style="left:38px;top:648px"><div class="obj" role="img" aria-label="Hemp oil bottle"></div></div>
  <div class="a prod" style="left:149px;top:648px"><div class="obj bud" role="img" aria-label="CBD bud"></div></div>
  <div class="a prod" style="left:260px;top:648px"><div class="obj" role="img" aria-label="Hemp oil bottle"></div></div>
  <div class="a prod" style="left:371px;top:648px"><div class="obj nug" role="img" aria-label="CBD flower"></div></div>
  <div class="a pname" style="left:38px;top:785px">Product Name<div class="price">$21.00</div></div>
  <div class="a pname" style="left:149px;top:785px">Product Name<div class="price">$21.00</div></div>
  <div class="a pname" style="left:260px;top:785px">Product Name<div class="price">$21.00</div></div>
  <div class="a pname" style="left:371px;top:785px">Product Name<div class="price">$21.00</div></div>
  <div class="a band" role="img" aria-label="Cannabis leaves"><h2>BEYOND THE HIGH</h2><div class="btn">Shop Now</div></div>
  <div class="a sect-icon" style="top:1062px"></div><div class="a sect-title" style="top:1080px">FEATURED PRODUCTS</div>
  <div class="a feat-img" role="img" aria-label="Jar of CBD oil with hemp leaf"></div>
  <div class="a feat"><h3>Lorem ipsum dolor</h3><div class="cost">$5.00</div><div class="qty">Quantity</div><div class="select"></div><div class="btn">Buy Now</div><div class="btn alt">Add To Cart</div><p>Lorem ipsum dolor sit amet, consectetur adipiscing elit, sed do eiusmod tempor incididunt ut labore et dolore magna aliqua. Ut enim ad minim veniam, quis nostrud exercitation ullamco laboris nisi ut aliquip ex ea commodo consequat. Duis aute irure dolor in reprehenderit in voluptate velit esse cillum dolore eu fugiat nulla pariatur. Excepteur sint occaecat cupidatat non proident, sunt in culpa qui officia deserunt mollit anim id est laborum</p></div>
  <div class="a sect-icon" style="top:1355px"></div><div class="a sect-title" style="top:1373px">BEST DEAL</div>
  <div class="deal" style="left:38px"><div class="obj mod" role="img" aria-label="Vape mod"></div><div class="deal-name">Product Name</div></div>
  <div class="deal" style="left:187px"><div class="obj dropper" role="img" aria-label="CBD oil with bud"></div><div class="deal-name">Product Name</div></div>
  <div class="deal" style="left:335px"><div class="obj" role="img" aria-label="Hemp oil bottle"></div><div class="deal-name">Product Name</div></div>
  <div class="a news"><div class="a sect-icon" style="top:50px"></div><div class="t">SUBSCRIBE OUR NEWSLETTER</div><p>Lorem ipsum dolor sit amet, consectetur adipiscing elit, sed do eiusmod tempor incididunt ut labore et dolore magna aliqua.</p><div class="field">Enter Your Email Address</div><div class="btn">Join</div></div>
  <footer class="a foot"><h4 style="left:38px">ABOUT US</h4><div class="about">Lorem ipsum dolor sit amet, consectetur adipiscing elit, sed do eiusmod tempor incididunt ut labore et dolore magna aliqua.</div><h4 style="left:213px">PRODUCTS</h4><ul style="left:213px"><li>CBD Flowers</li><li>CBD Vapes</li><li>HEMP Oils</li></ul><h4 style="left:327px">EXPLORE</h4><ul style="left:327px"><li>Home</li><li>About Us</li><li>Shop</li><li>Categories</li><li>Contact Us</li></ul><h4 style="left:436px">FOLLOW US</h4><ul style="left:436px"><li><span class="dot"></span>Pixelpost</li><li><span class="dot"></span>Chatterbox</li><li><span class="dot"></span>Snapgrid</li><li><span class="dot"></span>Worklink</li></ul><div class="pay"><span></span><span></span><span></span><span></span><span></span><span></span></div><div class="copy">© Copyrights 2021 The Company Name All Rights Reserved</div></footer>
</section>

</body>
</html>
```